Mortgage Company ready to make a statement!

We have a basic logo that I am fairly happy with ... but it could use a little bit of tweaking before we order the sign for our building. We also want some knock-your-socks-off business cards.
Problem: Inside of our Mortgage Office (Bright Fern Mortgage Group), we are going to have a coffee lounge (Sunbrew Cafe) for Realtors to use instead of the local Cuppington to meet with homebuyers. The office and coffee lounge are in an industrial building and is decorated with cozy overstuffed chairs, a hodge podge of interesting lamps and furniture, and goal is to make it as inviting as possible. However, we are a financial institution... so we need to keep it pretty clean as well.
One of my favorite marketing ideas is to cut a house key for everyone who buys a home using us with a key that matches our logo. There's only one key shape that works really well, so that needs to match the logo in order for the idea to work. I'll attach an image of the key blank.... although the way the key hole cut out looks terrible, so I was thinking of having them just do a thin outline instead.
Would like a similar, matching logo for the Sunbrew Cafe... but possibly something that would be a little less formal and would be cute on a coffee mug- nothing stuffy.
AND, we're opening a home inspection company as well, and we would like that logo and branding to match. The home inspection company is "Bright Fern Home Inspections"
We were thinking that for the home inspection company , we could use a magnifying glass shape inside of the house shape for the logo, use a keyhole shape inside of the same house for the mortgage company, and use a coffee cup inside of the house shape for Sunbrew Cafe.
Just getting stuck and need to help. I designed the attached logo myself, and that is what we are currently using. Designers at local printing companies have failed to impress us.
The mortgage industry has a lot of numbers and logos, etc that they require us to put on our business cards... so it's hard to keep them looking clean.
HELP! HELP! :)

```html
<!DOCTYPE html>
<html lang="en">
<head>
<meta charset="utf-8">
<title>Bright Fern Mortgage Group – Business Cards</title>
<link rel="stylesheet" href="https://fonts.googleapis.com/css2?family=Marcellus&family=Jost:wght@400;600&display=swap">
<style>
  :root{
    --brand-blue:#246789;
    --rule-slate:#4b4a5a;
    --card-white:#ffffff;
    --backdrop:#e8eaec;
    --ink-white:#ffffff;
  }
  *{margin:0;padding:0;box-sizing:border-box}
  html,body{width:1200px;height:900px;overflow:hidden}
  body{background:var(--backdrop);position:relative;font-family:"Jost",sans-serif}

  .card{position:absolute;left:300px;width:600px;height:343px;border-radius:22px;overflow:hidden;box-shadow:0 6px 18px rgba(0,0,0,.12)}
  .card--back{top:70px;background:var(--brand-blue);display:flex;align-items:center;justify-content:center}
  .card--front{top:468px;background:var(--card-white)}

  .back-wordmark{text-align:center;color:var(--ink-white)}
  .back-wordmark__name{font-family:"Marcellus",serif;font-size:44px;letter-spacing:1px;line-height:1}
  .back-wordmark__sub{font-family:"Jost",sans-serif;font-size:25px;letter-spacing:1.5px;margin-top:4px;display:inline-block;border-bottom:2px solid var(--ink-white);padding:0 6px 3px}

  .front-wordmark{position:absolute;left:44px;top:38px;color:var(--brand-blue)}
  .front-wordmark__name{font-family:"Marcellus",serif;font-size:40px;line-height:1;letter-spacing:.5px}
  .front-wordmark__sub{font-size:22px;letter-spacing:1.2px;margin-top:2px}

  .front-band{position:absolute;left:0;right:0;top:178px;bottom:0;background:var(--brand-blue);border-top:5px solid var(--rule-slate)}
  .holder{position:absolute;left:40px;top:24px;color:var(--ink-white)}
  .holder__name{font-family:"Marcellus",serif;font-size:24px;letter-spacing:1.5px}
  .holder__title{font-weight:600;font-size:13px;letter-spacing:1px;margin-top:2px}

  .contact{position:absolute;right:36px;bottom:26px;list-style:none;color:var(--ink-white);font-size:14.5px;letter-spacing:1.2px;line-height:1.55}
  .contact li{display:flex;align-items:center;gap:10px}
  .contact svg{width:13px;height:13px;flex:none;fill:var(--ink-white)}
</style>
</head>
<body>

<section class="card card--back" aria-label="Card back">
  <div class="back-wordmark">
    <div class="back-wordmark__name">BRIGHT FERN</div>
    <div class="back-wordmark__sub">Mortgage Group</div>
  </div>
</section>

<section class="card card--front" aria-label="Card front">
  <div class="front-wordmark">
    <div class="front-wordmark__name">BRIGHT FERN</div>
    <div class="front-wordmark__sub">Mortgage Group</div>
  </div>

  <div class="front-band">
    <div class="holder">
      <div class="holder__name">DANA WHITLOW</div>
      <div class="holder__title">CEO</div>
    </div>

    <ul class="contact">
      <li>
        <svg viewBox="0 0 16 16" aria-hidden="true"><path d="M3.6 1.5l2.2 2.8-1.3 1.6c.9 2 2.5 3.6 4.6 4.6l1.6-1.3 2.8 2.2-1.4 2.1C6.7 13.3 2.7 9.3 1.5 3z"/></svg>
        555-210-4387
      </li>
      <li>
        <svg viewBox="0 0 16 16" aria-hidden="true"><path d="M4.5 1h7v14h-7zM5.8 2.5v10h4.4v-10z"/></svg>
        000-123-4567
      </li>
      <li>
        <svg viewBox="0 0 16 16" aria-hidden="true"><path d="M4 1h8v4H4zM1.5 6h13v6H12v3H4v-3H1.5zM5.3 10.3v3.4h5.4v-3.4z"/></svg>
        000-123-4567
      </li>
      <li>
        <svg viewBox="0 0 16 16" aria-hidden="true"><path d="M1 3h14v10H1zM2.5 4.5v.3L8 8.8l5.5-4v-.3z"/></svg>
        dana.whitlow@brightfernmtg.com
      </li>
    </ul>
  </div>
</section>

</body>
</html>
```